IT Company needs full suite of stationery

Our company 4627 Vantor Holdings Inc. is an IT company based in Toronto, Canada. Based on our logo we would like to see business cards(front and back), letterhead, envelope, brochure template. Design would be simple, not too bright, modern but can be used for many years, good theme throughout. Our official logo is the the fullcolor_a, full company name is 4627 Vantor Holdings Inc., Please include full company name on all pieces. Logo can be modified to be the graphic only with the "4627 Holdings", I have cropped it myself for a couple files but I am no designer. We will provide lots of feedback so post early and often.

Project Deadline Extended
Reason: Very busy around the holidays, like a lot of the designs currently submitted, will definitely be picking one. Thanks for your submissions and merry Christmas and Happy New Year to everyone.

Industry/Entity Type

Business

```html
<!DOCTYPE html>
<html lang="en">
<head>
<meta charset="utf-8">
<title>4627 Holdings — Stationery Suite</title>
<link href="https://fonts.googleapis.com/css2?family=Open+Sans:wght@400;600;700&display=swap" rel="stylesheet">
<style>
  :root {
    --bg: #eceeed;
    --paper: #ffffff;
    --green: #4a9e45;
    --green-light: #7cbf4a;
    --green-dark: #3a8a3c;
    --green-faint: #e9f2e6;
    --ink: #4a4a4a;
    --ink-soft: #777777;
    --accent: #2bb3d6;
    --shadow: 0 6px 18px rgba(0,0,0,0.12);
  }
  * { margin: 0; padding: 0; box-sizing: border-box; }
  html, body { width: 1200px; height: 937px; overflow: hidden; }
  body {
    background: var(--bg);
    font-family: "Open Sans", Arial, sans-serif;
    color: var(--ink);
    position: relative;
  }
  .sheet {
    position: absolute;
    background: var(--paper);
    box-shadow: var(--shadow);
    overflow: hidden;
  }
  /* brand lockup */
  .brand { position: absolute; display: flex; align-items: center; }
  .brand-dot { border-radius: 50%; background: var(--green); flex: none; }
  .brand-name { font-weight: 700; color: var(--ink); white-space: nowrap; letter-spacing: 0.01em; }
  .faint-circle {
    position: absolute; border-radius: 50%;
    background: var(--green-faint);
  }

  /* letterhead */
  .letterhead { left: 185px; top: 66px; width: 388px; height: 546px; }
  .letterhead .brand { left: 20px; top: 27px; gap: 7px; }
  .letterhead .brand-dot { width: 38px; height: 38px; }
  .letterhead .brand-name { font-size: 15px; }
  .sender { position: absolute; right: 20px; top: 24px; text-align: right; font-size: 5px; line-height: 7px; color: var(--ink-soft); }
  .letter { position: absolute; left: 36px; top: 140px; width: 300px; font-family: Arial, sans-serif; font-size: 5px; line-height: 7.4px; color: #333; }
  .letter p { margin-bottom: 12px; position: relative; z-index: 1; }
  .letter .date { margin-bottom: 10px; }
  .letter .greet { margin-bottom: 6px; }
  .letter strong { font-weight: 700; }
  .signature-line { width: 28px; height: 12px; border-bottom: 1px solid #333; margin: 4px 0 6px; }
  .letterhead .faint-circle { left: 152px; top: 360px; width: 220px; height: 220px; }

  /* folder cover */
  .folder { left: 636px; top: 40px; width: 460px; height: 576px; }
  .folder .brand { left: 107px; top: 275px; gap: 14px; }
  .folder .brand-dot { width: 92px; height: 92px; }
  .folder .brand-name { font-size: 34px; }

  /* business cards */
  .card { width: 176px; height: 99px; }
  .card-front { left: 46px; top: 659px; }
  .card-front .brand { left: 12px; top: 14px; }
  .card-front .brand-dot { width: 36px; height: 36px; }
  .card-contact { position: absolute; right: 8px; top: 40px; text-align: right; font-size: 4.6px; line-height: 6.4px; color: var(--ink-soft); }
  .card-web { position: absolute; left: 8px; bottom: 8px; font-size: 4.6px; color: var(--accent); letter-spacing: 0.05em; }
  .card-back { left: 46px; top: 785px; }
  .card-back .brand { left: 10px; top: 59px; gap: 4px; }
  .card-back .brand-dot { width: 22px; height: 22px; }
  .card-back .brand-name { font-size: 9px; }
  .card-person { position: absolute; right: 8px; top: 71px; text-align: right; font-size: 6px; line-height: 7px; }
  .card-person .name { color: var(--accent); font-weight: 600; }
  .card-person .role { color: var(--ink-soft); }

  /* envelope front */
  .envelope-front { left: 265px; top: 673px; width: 432px; height: 208px; }
  .envelope-front .brand { left: 17px; top: 30px; gap: 6px; }
  .envelope-front .brand-dot { width: 34px; height: 34px; }
  .envelope-front .brand-name { font-size: 13px; }
  .envelope-front .faint-circle { left: 270px; top: 55px; width: 165px; height: 165px; }

  /* envelope back */
  .envelope-back { left: 737px; top: 673px; width: 432px; height: 206px; }
  .flap {
    position: absolute; left: 0; top: 0; width: 100%; height: 71px;
    background: linear-gradient(90deg, var(--green-dark), var(--green-light) 50%, var(--green-dark));
    border-radius: 0 0 40px 40px;
    display: flex; align-items: center; justify-content: center;
  }
  .flap-web { color: #fff; font-size: 10px; letter-spacing: 0.35em; font-weight: 600; }
</style>
</head>
<body>

  <section class="sheet letterhead">
    <div class="brand"><span class="brand-dot"></span><span class="brand-name">4627 Holdings</span></div>
    <div class="sender">
      88 Larkfield Ave<br>Toronto ON M4B 2K9<br>416.555.0193<br>dana@4627holdings.com
    </div>
    <div class="faint-circle"></div>
    <div class="letter">
      <p class="date">July 2, 2012</p>
      <p class="greet"><strong>Dear Client,</strong><br>ABC Building, def St., Country Name</p>
      <p>We are pleased to confirm the details of our recent discussion regarding your infrastructure review. Our team has prepared a full plan covering network upgrades, hosted services and ongoing support for your offices. The schedule outlined below keeps disruption low while giving your staff time to adapt to each change before the next phase begins.</p>
      <p>Please review the attached summary and let us know if any dates need to be adjusted on your side.</p>
      <p>Once approved, we will assign a dedicated project lead who will be your single point of contact throughout. Weekly reports will track progress, open items and upcoming tasks, and our service desk remains available at any time for urgent requests. We look forward to working with you on this project.</p>
      <p style="margin-bottom:2px">Best Regards,</p>
      <div class="signature-line"></div>
      <p><strong>Adrian Pell</strong><br>Director<br><br>ABC Building, def St., Country Name</p>
    </div>
  </section>

  <section class="sheet folder">
    <div class="brand"><span class="brand-dot"></span><span class="brand-name">4627 Holdings</span></div>
  </section>

  <section class="sheet card card-front">
    <div class="brand"><span class="brand-dot"></span></div>
    <div class="card-contact">88 Larkfield Ave<br>Toronto ON M4B 2K9<br>416.555.0193<br>dana@4627holdings.com</div>
    <div class="card-web">www.4627holdings.com</div>
  </section>

  <section class="sheet card card-back">
    <div class="brand"><span class="brand-dot"></span><span class="brand-name">4627 Holdings</span></div>
    <div class="card-person"><div class="name">Dana Whitlow</div><div class="role">Owner</div></div>
  </section>

  <section class="sheet envelope-front">
    <div class="faint-circle"></div>
    <div class="brand"><span class="brand-dot"></span><span class="brand-name">4627 Holdings</span></div>
  </section>

  <section class="sheet envelope-back">
    <div class="flap"><span class="flap-web">www.4627holdings.com</span></div>
  </section>

</body>
</html>
```